Business Card for a Dental Office

The design should communicate integrity, quality and reliability. We also want the card look elegant, simple, but still stand out, different from the traditional-dental-office business card.

Industry/Entity Type

Business

```html
<!DOCTYPE html>
<html lang="en">
<head>
<meta charset="utf-8">
<title>Harwell Dental Studio – Business Card</title>
<link href="https://fonts.googleapis.com/css2?family=Oswald:wght@500&family=Open+Sans:wght@400;600&display=swap" rel="stylesheet">
<style>
  :root {
    --canvas: #ece9e4;
    --card-white: #ffffff;
    --card-black: #050505;
    --ink: #111111;
    --gold: #d9c20f;
    --gold-light: #f2e23a;
    --gold-dark: #a8900a;
    --tagline: #c2a616;
    --line: #1a1a1a;
  }
  * { margin: 0; padding: 0; box-sizing: border-box; }
  html, body { width: 1200px; height: 1000px; overflow: hidden; }
  body {
    position: relative;
    background: var(--canvas);
    font-family: "Open Sans", Arial, sans-serif;
    color: var(--ink);
  }
  .card {
    position: absolute;
    left: 265px;
    width: 666px;
    height: 397px;
    overflow: hidden;
    box-shadow: 0 4px 14px rgba(0,0,0,0.25);
  }
  .card--front { top: 73px; background: var(--card-white); }
  .card--back { top: 532px; background: var(--card-black); }

  /* Front: brand block */
  .brand {
    position: absolute;
    left: 34px;
    top: 72px;
    display: flex;
    align-items: center;
    gap: 12px;
  }
  .brand__mark {
    width: 56px; height: 56px;
    background: var(--gold);
    flex: none;
  }
  .brand__text { display: flex; flex-direction: column; }
  .brand__name {
    font-family: "Oswald", "Arial Narrow", sans-serif;
    font-weight: 500;
    font-size: 30px;
    line-height: 1;
    color: var(--ink);
    letter-spacing: 0.2px;
    white-space: nowrap;
  }
  .brand__tagline {
    font-family: "Oswald", "Arial Narrow", sans-serif;
    font-weight: 500;
    font-size: 13.5px;
    letter-spacing: 2.6px;
    color: var(--tagline);
    margin-top: 3px;
    white-space: nowrap;
  }

  /* Front: person */
  .person { position: absolute; left: 33px; top: 203px; right: 33px; }
  .person__name { font-weight: 600; font-size: 20px; line-height: 1.2; }
  .person__role {
    display: flex; align-items: center; gap: 10px;
    font-size: 15px; margin-top: 2px;
  }
  .person__rule { flex: 1; height: 1.5px; background: var(--line); margin-top: 4px; }

  /* Front: contact list */
  .contact {
    position: absolute; left: 33px; top: 276px;
    list-style: none; font-size: 15px; line-height: 23px;
  }
  .contact__item { display: flex; align-items: center; gap: 7px; white-space: nowrap; }
  .contact__icon { width: 15px; height: 12px; fill: var(--gold); }

  .address {
    position: absolute; right: 33px; top: 296px;
    text-align: right; font-size: 15px; line-height: 24px;
    font-style: normal;
  }

  /* Front: footer band */
  .band { position: absolute; left: 0; right: 0; bottom: 0; height: 32px; display: flex; }
  .band__gold {
    width: 300px;
    background: linear-gradient(90deg, var(--gold-dark) 0%, var(--gold-light) 55%, var(--gold) 100%);
  }
  .band__black { flex: 1; background: var(--card-black); }

  /* Back */
  .back__brand {
    position: absolute; right: 33px; top: 300px;
    display: flex; align-items: center; gap: 12px;
  }
  .back__mark {
    width: 50px; height: 50px; flex: none;
    background: linear-gradient(160deg, var(--gold-light) 0%, var(--gold) 50%, var(--gold-dark) 100%);
  }
  .back__text { text-align: right; }
  .back__name {
    font-family: "Oswald", "Arial Narrow", sans-serif;
    font-weight: 500; font-size: 28px; line-height: 1;
    color: var(--card-white);
    white-space: nowrap;
  }
  .back__tagline {
    font-family: "Oswald", "Arial Narrow", sans-serif;
    font-weight: 500; font-size: 12.5px; letter-spacing: 2.3px;
    color: var(--tagline); margin-top: 4px;
    white-space: nowrap;
  }
</style>
</head>
<body>

<section class="card card--front" aria-label="Card front">
  <div class="brand">
    <div class="brand__mark"></div>
    <div class="brand__text">
      <span class="brand__name">HARWELL DENTAL STUDIO</span>
      <span class="brand__tagline">A BRIGHTER SMILE STARTS WITH CARE</span>
    </div>
  </div>

  <div class="person">
    <p class="person__name">Owen Castell, PHA</p>
    <p class="person__role"><span>President</span><span class="person__rule"></span></p>
  </div>

  <ul class="contact">
    <li class="contact__item">
      <svg class="contact__icon" viewBox="0 0 16 12" aria-hidden="true"><path d="M1 4c0-2 3-3 7-3s7 1 7 3v1h-4V3.5H5V5H1z M3 6h10l1 5H2z"/></svg>
      <span>+ 000 000 0000</span>
    </li>
    <li class="contact__item">
      <svg class="contact__icon" viewBox="0 0 16 12" aria-hidden="true"><path d="M4 0h8v3H4z M1 4h14v5h-3v3H4V9H1z M5 8v3h6V8z"/></svg>
      <span>+ 000 000 0000</span>
    </li>
    <li class="contact__item">
      <svg class="contact__icon" viewBox="0 0 16 12" aria-hidden="true"><path d="M1 1h14v1L8 7 1 2z M1 3.5l7 5 7-5V11H1z"/></svg>
      <span>info@harwelldentalstudio.com</span>
    </li>
  </ul>

  <address class="address">
    Level 14, 88 Harbour Crest<br>
    Sydney, New South Wales
  </address>

  <div class="band">
    <div class="band__gold"></div>
    <div class="band__black"></div>
  </div>
</section>

<section class="card card--back" aria-label="Card back">
  <div class="back__brand">
    <div class="back__mark"></div>
    <div class="back__text">
      <p class="back__name">HARWELL DENTAL STUDIO</p>
      <p class="back__tagline">A BRIGHTER SMILE STARTS WITH CARE</p>
    </div>
  </div>
</section>

</body>
</html>
```